Brightmill Data Works

Our company is about IT hardwares and IT solutions. IT hardware such as PC, RAMS, storage and servers. IT solutions such as project management, BA. We are also selling new technology too.

Target Market(s)

Consumer, Small to Medium Business, Corporate

Requirements
Must have
• The business card must have the following:
• Name:
• Title:
• Contact Number:
• Email address:
• Website:
• Color: Must match the logo color upgrade

```html
<!DOCTYPE html>
<html lang="en">
<head>
<meta charset="utf-8">
<title>Brightmill Data Works – Business Card</title>
<link href="https://fonts.googleapis.com/css2?family=Roboto+Condensed:wght@400;700&display=swap" rel="stylesheet">
<style>
  :root {
    --backdrop: #ece9e4;
    --card: #ffffff;
    --panel-dark: #4b4b4b;
    --panel-light: #6e6e6e;
    --accent: #e08a2a;
    --accent-deep: #c8701c;
    --ink: #3a3a3a;
    --panel-text: #ffffff;
    --pattern-a: #fbf1e8;
    --pattern-b: #f6e6d6;
  }
  * { margin: 0; padding: 0; box-sizing: border-box; }
  html, body {
    width: 1200px; height: 950px; overflow: hidden;
    background: var(--backdrop);
    font-family: "Roboto Condensed", "Arial Narrow", sans-serif;
  }
  .canvas { position: relative; width: 1200px; height: 950px; }
  .card {
    position: absolute;
    width: 700px; height: 400px;
    background: var(--card);
    box-shadow: 0 6px 18px rgba(0,0,0,0.18);
    overflow: hidden;
  }
  .card--front { left: 250px; top: 55px; }
  .card--back  { left: 250px; top: 495px; }

  /* front */
  .contact-panel {
    position: absolute; left: 0; top: 120px;
    width: 322px; height: 170px;
    background: linear-gradient(90deg, var(--panel-light), var(--panel-dark));
    padding: 26px 0 0 44px;
    color: var(--panel-text);
  }
  .contact-panel__name {
    color: var(--accent);
    font-size: 24px; font-weight: 400; letter-spacing: 0.5px;
    line-height: 1;
  }
  .contact-panel__title {
    font-size: 17px; margin-top: 6px; margin-bottom: 14px;
  }
  .contact-list { list-style: none; }
  .contact-list__item {
    display: flex; align-items: center; gap: 9px;
    font-size: 16px; line-height: 25px;
  }
  .contact-list__icon { width: 13px; height: 13px; flex: none; }

  .brand {
    position: absolute; left: 420px; top: 160px;
    display: flex; align-items: center; gap: 12px;
  }
  .brand__mark { width: 22px; height: 22px; background: var(--accent); flex: none; }
  .brand__name {
    font-size: 30px; font-weight: 700; color: var(--ink);
    line-height: 1.05; letter-spacing: 0.5px; text-transform: uppercase;
  }

  /* back */
  .card__pattern {
    position: absolute; inset: 0;
    background: linear-gradient(135deg, var(--pattern-a), var(--pattern-b) 50%, var(--pattern-a));
  }
  .back-brand {
    position: absolute; left: 0; right: 0; top: 0; bottom: 0;
    display: flex; align-items: center; justify-content: center;
  }
  .back-brand__name {
    font-size: 30px; font-weight: 700; color: var(--accent-deep);
    letter-spacing: 0.5px; text-transform: uppercase;
  }
</style>
</head>
<body>
<main class="canvas">

  <section class="card card--front" aria-label="Business card front">
    <div class="contact-panel">
      <p class="contact-panel__name">MARA ELLWOOD</p>
      <p class="contact-panel__title">CEO/FOUNDER</p>
      <ul class="contact-list">
        <li class="contact-list__item">
          <svg class="contact-list__icon" viewBox="0 0 16 16" aria-hidden="true">
            <path d="M3 1l3 3-1.6 2.2a9 9 0 0 0 5.4 5.4L12 10l3 3-2 2.5C6.5 15 1 9.5 0.5 3z" fill="#e08a2a"/>
          </svg>
          <span>614 208 7391</span>
        </li>
        <li class="contact-list__item">
          <svg class="contact-list__icon" viewBox="0 0 16 16" aria-hidden="true">
            <rect x="1" y="3" width="14" height="10" rx="1" fill="#e08a2a"/>
            <path d="M1.5 4l6.5 5 6.5-5" fill="none" stroke="#4b4b4b" stroke-width="1.3"/>
          </svg>
          <span>mara@brightmilldata.com</span>
        </li>
        <li class="contact-list__item">
          <svg class="contact-list__icon" viewBox="0 0 16 16" aria-hidden="true">
            <circle cx="8" cy="8" r="7" fill="#e08a2a"/>
            <path d="M1 8h14M8 1c3 3 3 11 0 14M8 1c-3 3-3 11 0 14" fill="none" stroke="#4b4b4b" stroke-width="1"/>
          </svg>
          <span>www.brightmilldata.com</span>
        </li>
      </ul>
    </div>

    <div class="brand">
      <span class="brand__mark" aria-hidden="true"></span>
      <p class="brand__name">Brightmill<br>Data Works</p>
    </div>
  </section>

  <section class="card card--back" aria-label="Business card back">
    <div class="card__pattern" role="img" aria-label="Faint repeating brand pattern in light peach"></div>
    <div class="back-brand">
      <p class="back-brand__name">Brightmill Data Works</p>
    </div>
  </section>

</main>
</body>
</html>
```